Telvo Website - endlich neu?!
Aufgabenstellung
Es geht um die Gestaltung der Startseite auf Basis unseres verwendeten Magento-Templates.
Außerdem um die Gestaltung von Visitenkarte und Briefkopf.

```html
<!DOCTYPE html>
<html lang="de">
<head>
<meta charset="utf-8">
<title>Telvo – die Jackenerweiterung</title>
<link href="https://fonts.googleapis.com/css2?family=Roboto:wght@300;400&family=Dawning+of+a+New+Day&display=swap" rel="stylesheet">
<style>
:root{
  --bar:#a3a3a3;
  --ink:#111;
  --soft:#b5b5b5;
  --red:#e01b1b;
  --white:#fff;
}
*{box-sizing:border-box;margin:0;padding:0}
html,body{width:983px;height:1200px;overflow:hidden;background:var(--white)}
body{position:relative;font-family:"Roboto",Arial,sans-serif;color:var(--ink)}
.abs{position:absolute}
.brand{left:52px;top:14px}
.brand-name{font-weight:400;font-size:64px;letter-spacing:-1px;color:var(--ink);line-height:1}
.tagline{left:322px;top:28px;font-weight:300;font-size:27px;letter-spacing:-0.5px}
.subline{left:322px;top:58px;font-family:"Dawning of a New Day",cursive;font-size:25px;color:var(--soft);white-space:nowrap}
.toplinks{right:12px;top:15px;display:flex;gap:14px;font-size:12.5px}
.toplinks span{display:flex;align-items:center;gap:5px}
.radio{width:15px;height:15px;border-radius:50%;border:3px solid var(--soft);background:var(--white)}
.radio.on{border-color:var(--ink);background:var(--red)}
.nav{left:50px;top:106px;width:883px;height:38px;background:var(--bar);border-radius:4px;display:flex;justify-content:space-between;align-items:center;padding:0 28px 0 22px;font-weight:300;font-size:22px;color:var(--white)}
.nav .current{color:var(--ink)}
.hero{left:50px;top:173px;width:883px;height:336px;border-radius:8px;overflow:hidden;background:linear-gradient(120deg,#8a3a48 0%,#c99aa8 30%,#2a2a2e 60%,#9a9282 100%)}
.hero-claim{position:absolute;right:30px;top:180px;text-align:right;font-weight:300;font-size:66px;line-height:68px;color:var(--white);letter-spacing:-2px}
.intro{left:50px;top:525px;width:883px;font-size:13px;line-height:17.3px;text-align:justify}
.step{width:212px;height:212px;border-radius:50%;border:10px solid var(--bar)}
.step1{left:79px;top:726px;background:linear-gradient(135deg,#8b3444,#6e2434 60%,#2b2b2b)}
.step2{left:388px;top:726px;background:linear-gradient(135deg,#1e1e22 30%,#2f7d86 55%,#8b3444 70%)}
.step3{left:697px;top:726px;background:linear-gradient(135deg,#d9b7a3 20%,#c43f77 45%,#2a2a2e 70%,#8b3444)}
.note{font-family:"Dawning of a New Day",cursive;font-size:22px;color:#999;line-height:24px}
.newsletter{left:50px;top:989px;width:883px;height:38px;background:var(--bar);border-radius:4px;display:flex;align-items:center;padding-left:22px}
.newsletter-title{font-weight:300;font-size:22px;color:var(--white);margin-right:8px}
.newsletter-field{width:192px;height:20px;border-radius:10px;background:var(--white);font-size:9px;color:#999;display:flex;align-items:center;justify-content:center}
.go{width:17px;height:17px;border-radius:50%;border:4px solid var(--ink);background:var(--white);margin-left:10px}
.totop{position:absolute;right:10px;top:11px;font-size:12.5px;display:flex;align-items:center;gap:5px}
.totop svg{display:block}
.col{top:1054px;font-size:12px;line-height:17.3px}
.col h3{font-weight:300;font-size:16px;color:var(--soft);margin-bottom:8px}
.like{left:701px;top:1056px;width:86px;height:20px;background:#eceef4;border:1px solid #c7cbd6;border-radius:2px}
.social{left:806px;top:1059px;font-size:12px;display:flex;align-items:center;gap:7px}
.social i{width:15px;height:15px;border-radius:50%;background:var(--red);border:3px solid var(--ink)}
</style>
</head>
<body>
<header>
  <div class="abs brand"><span class="brand-name">Telvo</span></div>
  <div class="abs tagline">die Jackenerweiterung</div>
  <div class="abs subline">Babybauch oder Nachwuchs tragen ohne Abschied von der Lieblingsjacke</div>
  <div class="abs toplinks">
    <span><i class="radio"></i>English</span>
    <span><i class="radio"></i>Wunschliste</span>
    <span><i class="radio on"></i>Log In</span>
    <span><i class="radio"></i>Sign Up</span>
  </div>
  <nav class="abs nav">
    <span class="current">Start</span><span>Was ist Telvo</span><span>Rund um Telvo</span><span>Shop</span><span>Handler</span>
  </nav>
</header>

<section class="abs hero" role="img" aria-label="Foto: Baby mit Streifenmütze schläft warm eingepackt in der Jacke der Mutter">
  <div class="hero-claim">wohlig warm<br>auf dem Arm</div>
</section>

<p class="abs intro">Lorem ipsum dolor sit amet, consectetuer adipiscing elit. Aenean commodo ligula eget dolor. Aenean massa. Cum sociis natoque penatibus et magnis dis parturient montes, nascetur ridiculus mus. Donec quam felis, ultricies nec, pellentesque eu, pretium quis, sem. Nulla consequat massa quis enim. Donec pede justo, fringilla vel, aliquet nec, vulputate eget, arcu. In enim justo, rhoncus ut, imperdiet a, venenatis vitae, justo. Nullam dictum felis eu pede mollis pretium. Integer tincidunt. Cras dapibus. Vivamus elementum semper nisi. Aenean vulputate eleifend tellus. Aenean leo ligula, porttitor eu, consequat vitae, eleifend ac, enim. Aliquam lorem ante, dapibus in, viverra quis, feugiat a, tellus. Phasellus viverra nulla ut metus varius laoreet. Quisque rutrum. Aenean imperdiet. Etiam ultricies nisi vel augue. Curabitur ullamcorper ultricies nisi. Nam eget dui. Etiam rhoncus. Maecenas tempus, tellus eget condimentum rhoncus, sem quam semper libero, sit amet adipiscing sem neque sed ipsum. Nam quam nunc, blandit vel, luctus pulvinar, hendrerit id, lorem. Maecenas nec odio et ante tincidunt tempus. Donec vitae sapien ut libero venenatis faucibus. Nullam quis ante. Etiam sit amet orci eget eros faucibus tincidunt. Duis leo. Sed fringilla mauris sit amet nibh. Donec sodales sagittis magna.</p>

<section class="steps">
  <div class="abs note" style="left:78px;top:700px">nimm deine Jacke</div>
  <div class="abs step step1" role="img" aria-label="Foto: Person in weinroter Jacke"></div>
  <div class="abs step step2" role="img" aria-label="Foto: Reißverschluss von Jacke und Einsatz wird verbunden"></div>
  <div class="abs step step3" role="img" aria-label="Foto: Baby schläft eingepackt in der erweiterten Jacke"></div>
  <div class="abs note" style="left:582px;top:726px">wohlfuehlen ...</div>
  <div class="abs note" style="left:244px;top:920px;width:200px;text-align:center">zippe deine Jacke und Telvo zusammen</div>
</section>

<section class="abs newsletter">
  <span class="newsletter-title">Newsletter bestellen</span>
  <span class="newsletter-field">Emailadresse eintragen</span>
  <span class="go"></span>
  <span class="totop">Top
    <svg width="17" height="17" viewBox="0 0 17 17"><circle cx="8.5" cy="8.5" r="8" fill="var(--white)"/><path d="M4 11 L8.5 5 L13 11Z" fill="var(--ink)"/></svg>
  </span>
</section>

<footer>
  <div class="abs col" style="left:51px"><h3>Company</h3>Uber uns<br>Blog<br>Presse<br>Partner<br>Jobs</div>
  <div class="abs col" style="left:167px"><h3>Hilfe</h3>Kontakt<br>FAQ<br>Versand<br>Kontakt<br>Ruckgabe</div>
  <div class="abs col" style="left:252px"><h3>Follow</h3>Freundebuch<br>Zwitscherpost</div>
  <div class="abs col" style="left:342px"><h3>Adresse</h3>Marlene Oswin<br>Lindenhofweg 7 , 40210 Rheinfeld<br>Germany</div>
  <div class="abs like" aria-hidden="true"></div>
  <div class="abs social"><i></i>Telvo auf Freundebuch</div>
</footer>
</body>
</html>
```